KRV Cartridge chip board folding ammuniton boxes for retail sale

Design a scalable design for use with 20 round and 50 round boxes for Ammunition. The caliber will be 9mm but will need to be editable, all warnings and barcodes will need to be able to be edited also. I have attached the company logo.

**UPDATE**
Box dimensions
20rd= 2.55in long X 2.1in width X 1.25in height

50rd= 5.1in long x 2.6in width X 1.2in height

Please see the bullet picture i would like used if possible.

Target Market(s)

Quality shooting sports, self defense

Industry/Entity Type

Self Defense

Requirements
Must have
• supplied company logo design
Should not have
• any cartoons of any kind

```html
<!DOCTYPE html>
<html lang="en">
<head>
<meta charset="utf-8">
<title>KRV Cartridge – 9mm Box Panels</title>
<link rel="stylesheet" href="https://fonts.googleapis.com/css2?family=Montserrat:wght@600;700;800;900&display=swap">
<style>
  :root{
    --red:#d3161d;
    --red-deep:#9c0e13;
    --red-dark:#7d0a0e;
    --ink:#1d1d1f;
    --headline:#2b2b2e;
    --steel:#8c8c90;
    --paper:#ffffff;
    --stage:#f1f1f2;
  }
  *{box-sizing:border-box;margin:0;padding:0}
  html,body{width:1200px;height:750px;overflow:hidden;background:var(--stage);
    font-family:"Montserrat",Arial,sans-serif;color:var(--ink)}
  .canvas{position:relative;width:1200px;height:750px}
  .panel{position:absolute;overflow:hidden;background:var(--paper);
    box-shadow:0 6px 18px rgba(0,0,0,.12)}
  .panel > svg{position:absolute;inset:0;width:100%;height:100%}

  /* panel positions */
  .top-50{left:40px;top:24px;width:660px;height:130px}
  .top-20{left:740px;top:24px;width:420px;height:130px}
  .front-50{left:40px;top:174px;width:660px;height:300px}
  .front-20{left:740px;top:174px;width:420px;height:300px}
  .end-50{left:40px;top:494px;width:336px;height:156px}
  .end-20{left:420px;top:494px;width:280px;height:156px}

  .lid{background:linear-gradient(100deg,var(--red-dark) 0%,var(--red) 45%,var(--red) 65%,var(--red-deep) 100%)}

  .brand{position:absolute;display:flex;align-items:center;gap:8px;
    font-weight:800;color:var(--ink);white-space:nowrap;letter-spacing:.01em}
  .brand.on-red{color:var(--paper)}
  .brand-ring{border:3px solid var(--red);border-radius:50%;flex:none}
  .brand.on-red .brand-ring{border-color:var(--paper)}

  .headline{position:absolute;font-weight:900;color:var(--headline);text-transform:uppercase;
    line-height:.92;letter-spacing:.01em;white-space:nowrap}

  .count-badge{position:absolute;background:var(--red-deep);color:var(--paper);
    text-align:center;font-weight:700;line-height:1}
  .count-badge .count-number{display:block;font-weight:800}
  .count-badge.light{background:var(--paper);color:var(--red);border:2px solid var(--red-deep)}

  .spec{position:absolute;color:var(--paper);text-align:center;transform:rotate(-8deg);
    transform-origin:center;line-height:1.15;white-space:nowrap}
  .spec .caliber{display:block;font-weight:800}
  .spec .type{display:block;font-weight:700}

  .lid-caliber{position:absolute;color:var(--paper);font-weight:800;white-space:nowrap}
  .lid-type{position:absolute;color:var(--paper);font-weight:700;line-height:1.2;
    text-align:center;white-space:nowrap}

  .round-image{position:absolute;border-radius:8px 8px 4px 4px;
    background:linear-gradient(180deg,#c87a3a 0%,#e3a060 14%,#8d8a78 30%,#b4b19e 55%,#6f6c5e 88%,#a88d4f 100%)}

  .end-spec{position:absolute;color:var(--ink);line-height:1.15}
  .end-spec .caliber{display:block;font-weight:800}
  .end-spec .type{display:block;font-weight:700;font-size:9px}
</style>
</head>
<body>
<main class="canvas">

  <!-- 50 round top panel -->
  <section class="panel lid top-50">
    <p class="lid-caliber" style="left:26px;top:50px;font-size:22px">9mm 115gr</p>
    <div class="brand on-red" style="left:228px;top:24px;font-size:24px">
      <span>KRV Cartridge</span><span class="brand-ring" style="width:26px;height:26px"></span>
    </div>
    <p class="lid-type" style="left:228px;top:68px;width:210px;font-size:12px">FULL METAL JACKET<br>FMJ / ELITE AMMUNITION</p>
    <div class="count-badge light" style="right:24px;top:30px;width:70px;height:70px;padding-top:9px;font-size:10px">
      <span class="count-number" style="font-size:30px">50</span>Cartridge<br>per box
    </div>
  </section>

  <!-- 20 round top panel -->
  <section class="panel lid top-20">
    <p class="lid-caliber" style="left:20px;top:54px;font-size:17px">9mm 115gr</p>
    <div class="brand on-red" style="left:140px;top:26px;font-size:19px">
      <span>KRV Cartridge</span><span class="brand-ring" style="width:20px;height:20px"></span>
    </div>
    <p class="lid-type" style="left:140px;top:64px;width:170px;font-size:10px">FULL METAL JACKET<br>FMJ / ELITE AMMUNITION</p>
    <div class="count-badge light" style="right:18px;top:34px;width:60px;height:62px;padding-top:8px;font-size:9px">
      <span class="count-number" style="font-size:26px">20</span>Cartridge<br>per box
    </div>
  </section>

  <!-- 50 round front panel -->
  <section class="panel front-50">
    <svg viewBox="0 0 660 300" preserveAspectRatio="none" aria-hidden="true">
      <defs>
        <linearGradient id="red50" x1="0" y1="0" x2="1" y2="1">
          <stop offset="0" stop-color="#a50f14"/><stop offset=".5" stop-color="#d3161d"/><stop offset="1" stop-color="#a50f14"/>
        </linearGradient>
      </defs>
      <path d="M0 225 C220 202 420 152 660 122 L660 142 C420 172 220 222 0 243 Z" fill="#8c8c90"/>
      <path d="M0 237 C220 214 420 164 660 134 L660 300 L0 300 Z" fill="url(#red50)"/>
    </svg>
    <div class="brand" style="left:212px;top:24px;font-size:26px">
      <span>KRV Cartridge</span><span class="brand-ring" style="width:30px;height:30px"></span>
    </div>
    <h1 class="headline" style="left:36px;top:88px;font-size:36px">Elite<br>Performance<br>Ammunition</h1>
    <div class="count-badge" style="right:28px;top:16px;width:70px;height:70px;padding-top:8px;font-size:10px">
      <span class="count-number" style="font-size:32px">50</span>Cartridge<br>per box
    </div>
    <div class="round-image" role="img" aria-label="Photo of a 9mm cartridge with copper bullet" style="left:560px;top:104px;width:50px;height:150px"></div>
    <p class="spec" style="left:290px;top:202px;width:260px">
      <span class="caliber" style="font-size:26px">9mm 115gr</span>
      <span class="type" style="font-size:12px">FULL METAL JACKET</span>
      <span class="type" style="font-size:12px">FMJ / ELITE AMMUNITION</span>
    </p>
  </section>

  <!-- 20 round front panel -->
  <section class="panel front-20">
    <svg viewBox="0 0 420 300" preserveAspectRatio="none" aria-hidden="true">
      <defs>
        <linearGradient id="red20" x1="0" y1="0" x2="1" y2="1">
          <stop offset="0" stop-color="#a50f14"/><stop offset=".5" stop-color="#d3161d"/><stop offset="1" stop-color="#a50f14"/>
        </linearGradient>
      </defs>
      <path d="M0 212 C150 196 280 172 420 152 L420 170 C280 190 150 214 0 230 Z" fill="#8c8c90"/>
      <path d="M0 224 C150 208 280 184 420 164 L420 300 L0 300 Z" fill="url(#red20)"/>
    </svg>
    <div class="brand" style="left:40px;top:26px;font-size:22px">
      <span>KRV Cartridge</span><span class="brand-ring" style="width:24px;height:24px"></span>
    </div>
    <h2 class="headline" style="left:24px;top:90px;font-size:27px">Elite<br>Performance<br>Ammunition</h2>
    <div class="count-badge" style="right:20px;top:16px;width:60px;height:60px;padding-top:7px;font-size:9px">
      <span class="count-number" style="font-size:26px">20</span>Cartridge<br>per box
    </div>
    <div class="round-image" role="img" aria-label="Photo of a 9mm cartridge with copper bullet" style="left:346px;top:92px;width:42px;height:128px"></div>
    <p class="spec" style="left:90px;top:212px;width:240px">
      <span class="caliber" style="font-size:24px">9mm 115gr</span>
      <span class="type" style="font-size:11px">FULL METAL JACKET</span>
      <span class="type" style="font-size:11px">FMJ / ELITE AMMUNITION</span>
    </p>
  </section>

  <!-- 50 round end panel -->
  <section class="panel end-50">
    <svg viewBox="0 0 336 156" preserveAspectRatio="none" aria-hidden="true">
      <rect x="0" y="0" width="336" height="96" fill="#c1141a"/>
      <rect x="0" y="96" width="336" height="8" fill="#8c8c90"/>
    </svg>
    <div class="count-badge light" style="left:14px;top:14px;width:58px;height:64px;padding-top:8px;font-size:9px">
      <span class="count-number" style="font-size:24px">50</span>Cartridge<br>per box
    </div>
    <div class="brand on-red" style="left:96px;top:32px;font-size:20px">
      <span>KRV Cartridge</span><span class="brand-ring" style="width:22px;height:22px"></span>
    </div>
    <p class="end-spec" style="left:16px;top:112px">
      <span class="caliber" style="font-size:16px">9mm 115gr</span>
      <span class="type">FULL METAL JACKET · FMJ / ELITE AMMUNITION</span>
    </p>
  </section>

  <!-- 20 round end panel -->
  <section class="panel end-20">
    <svg viewBox="0 0 280 156" preserveAspectRatio="none" aria-hidden="true">
      <rect x="0" y="0" width="280" height="96" fill="#c1141a"/>
      <rect x="0" y="96" width="280" height="8" fill="#8c8c90"/>
    </svg>
    <div class="count-badge light" style="left:14px;top:14px;width:58px;height:64px;padding-top:8px;font-size:9px">
      <span class="count-number" style="font-size:24px">20</span>Cartridge<br>per box
    </div>
    <div class="brand on-red" style="left:88px;top:34px;font-size:16px">
      <span>KRV Cartridge</span><span class="brand-ring" style="width:18px;height:18px"></span>
    </div>
    <p class="end-spec" style="left:16px;top:112px">
      <span class="caliber" style="font-size:16px">9mm 115gr</span>
      <span class="type">FULL METAL JACKET · FMJ / ELITE AMMUNITION</span>
    </p>
  </section>

</main>
</body>
</html>
```